Web Design Project

We are looking for a unified design of Corporate Website, Stationary (Including Letterhead and Envelopes), Business Cards, Email Footers and Sales & Marketing Brochures.

Color palette should include:
Black (R: 24, G:24, B:24)
Red (R:206, G:0, B:39)
Dark Grey (R:51, G:51, B:51)
Light Grey/Silver (R:203, G:203, B:203)

As we do business in North America and the UK, designs should be reflective of standard sizing for both regions.

Check out our website to better understand who we are: www.KLVR.com and a copy of our Logo has been uploaded for reference.
Updates

Hello all, we had not anticipated the volume of unique, high quality designs we have received, thank you all for your submissions. A team review of all designs will take place the week of December 8th, and final decisions and selections made. Thank you again

Target Market(s)

Automotive Parts Wholesalers, Vehicle Repair Specialists, Automotive Parts Manufacturers, Automotive Insurance

Industry/Entity Type

Business

Font styles to use
Sans Serif

Requirements
Must have
• - Color palette should include:
- Black (R: 24, G:24, B:24)
- Red (R:206, G:0, B:39)
- Dark Grey (R:51, G:51, B:51)
- Light Grey/Silver (R:203, G:203, B:203)
Should not have
• No Animations

```html
<!DOCTYPE html>
<html lang="en">
<head>
<meta charset="utf-8">
<title>Meridian Parts Solutions</title>
<link href="https://fonts.googleapis.com/css2?family=Hind:wght@300;400;500;600&display=swap" rel="stylesheet">
<style>
:root{
  --black:#181818;
  --red:#ce0027;
  --dark:#333333;
  --silver:#cbcbcb;
  --panel:#f1f1f1;
  --text:#555555;
  --white:#ffffff;
}
*{box-sizing:border-box;margin:0;padding:0}
html,body{width:983px;height:1200px;overflow:hidden;background:var(--white);font-family:"Hind",sans-serif;color:var(--text)}
.page{position:relative;width:983px;height:1200px}
.masthead{position:absolute;left:0;top:0;width:983px;height:408px;background:linear-gradient(135deg,#2a2a2a 0%,#4a4a4a 45%,#2e2e2e 75%,#3a3a3a 100%)}
.utility{position:absolute;right:134px;top:10px;font-size:8.5px;color:#bbb;letter-spacing:.2px}
.utility span{margin:0 3px}
.brand{position:absolute;left:131px;top:24px;display:flex;align-items:center;gap:9px}
.brand-mark{width:48px;height:48px;border-radius:50%;background:#8a8a8a}
.brand-name{font-size:25px;font-weight:600;color:var(--white);line-height:1;letter-spacing:.5px}
.contact{position:absolute;right:142px;top:42px;text-align:right;color:var(--white)}
.contact .label{font-size:13px;font-weight:300;display:block}
.contact .phone{display:flex;align-items:center;gap:6px;font-size:17px;font-weight:400;margin-top:-1px}
.nav{position:absolute;left:131px;top:90px;width:718px;height:39px;background:var(--red);display:flex;align-items:center;padding-left:6px}
.nav a{color:var(--white);text-decoration:none;font-size:11.5px;font-weight:500;padding:0 10.5px;line-height:39px;border-right:1px solid rgba(0,0,0,.15)}
.nav a:last-child{border-right:none}
.hero{position:absolute;left:131px;top:129px;width:718px;height:326px;background:linear-gradient(#fafafa,#eeeeee);border:1px solid #e0e0e0;border-top:none}
.hero-title{position:absolute;left:45px;top:98px;font-size:30px;font-weight:500;color:var(--black);letter-spacing:.3px}
.hero-sub{position:absolute;left:45px;top:137px;font-size:18px;font-weight:500;color:var(--red)}
.hero-copy{position:absolute;left:49px;top:166px;font-size:9.5px;line-height:15px;color:#666;width:300px}
.dots{position:absolute;left:49px;top:206px;display:flex;gap:2px}
.dots i{width:10px;height:10px;border-radius:50%;background:#777;display:block}
.hero-art{position:absolute;left:394px;top:56px;width:262px;height:210px;border-radius:40px;background:radial-gradient(circle at 50% 45%,#c8c8c8,#6e6e6e 70%,#eeeeee 72%)}
.tiles{position:absolute;left:131px;top:480px;display:flex;gap:3px}
.tile{position:relative;width:237px;height:142px;overflow:hidden;box-shadow:0 10px 10px -8px rgba(0,0,0,.25)}
.tile-photo{position:absolute;inset:0}
.tile-caption{position:absolute;left:0;bottom:0;width:100%;height:37px;background:rgba(30,30,30,.72);color:var(--white);font-size:17px;font-weight:400;padding:9px 0 0 16px;display:flex;justify-content:space-between}
.tile-caption svg{margin-right:10px;margin-top:2px}
.about{position:absolute;left:128px;top:676px;width:240px}
.about h2{font-size:19.5px;font-weight:500;color:var(--red);margin-bottom:6px}
.about p{font-size:9.8px;line-height:15.3px;color:#555;margin-bottom:5px}
.about p.tight{margin-bottom:0}
.video{position:absolute;left:393px;top:683px;width:215px}
.video-frame{position:relative;width:215px;height:115px;background:linear-gradient(135deg,#5b5a57,#a29f98 45%,#3e3c3a)}
.play{position:absolute;left:90px;top:40px}
.video h3{font-size:17px;font-weight:400;color:#333;margin-top:9px}
.video p{font-size:9.8px;line-height:15.3px;color:#666;margin-top:2px}
.news{position:absolute;left:636px;top:678px;width:215px}
.news h3{font-size:17px;font-weight:400;color:#333;margin-bottom:6px}
.news h4{font-size:11px;font-weight:400;color:var(--red)}
.news p{font-size:8.8px;line-height:13.6px;color:#777;margin-top:2px}
.news .more{font-size:10.5px;color:var(--black);display:block;margin:4px 0 14px}
.badges{position:absolute;left:138px;top:912px;width:694px;display:flex;justify-content:space-between;align-items:center}
.badge{height:20px;background:#9a9a9a;border-radius:10px}
.footer{position:absolute;left:0;top:957px;width:983px;height:189px;background:linear-gradient(#4a4a4a,#2c2c2c)}
.col{position:absolute;top:31px}
.col h5{font-size:14px;font-weight:400;color:var(--white);margin-bottom:2px}
.col a{display:block;font-size:10.5px;color:#e8e8e8;text-decoration:none;line-height:19.6px}
.col p{font-size:8.8px;color:#ddd;margin-top:2px}
.divider{position:absolute;top:34px;width:1px;height:93px;background:#5c5c5c}
.social{display:flex;gap:3px;margin-top:8px}
.social i{width:21px;height:21px;border-radius:50%;background:var(--white);display:block}
.legal{position:absolute;left:0;top:1146px;width:983px;height:54px;background:#2a2a2a;color:#aaa;font-size:9.3px;padding:17px 0 0 151px}
.legal span{margin-right:5px}
</style>
</head>
<body>
<div class="page">
  <header class="masthead">
    <div class="utility">CDN<span>|</span>UK<span>|</span>USA<span>|</span>SUPPLIER LOGIN<span>|</span>MERIDIAN AWARDS</div>
    <div class="brand"><span class="brand-mark"></span><span class="brand-name">Meridian Parts Solutions</span></div>
    <div class="contact">
      <span class="label">Contact Us</span>
      <span class="phone">
        <svg width="20" height="20" viewBox="0 0 20 20"><circle cx="10" cy="10" r="9" fill="none" stroke="#aaa" stroke-width="1.2"/><path d="M7 5.5c-.8.5-1.3 1.5-.9 2.7.8 2.4 2.6 4.5 4.9 5.6 1.1.5 2.1.1 2.7-.7l-1.4-1.6-1.2.6c-1-.6-1.9-1.6-2.4-2.7l.8-1.1z" fill="#aaa"/></svg>
        555.014.2270
      </span>
    </div>
  </header>

  <nav class="nav">
    <a>HOME</a><a>INTELLIGENT SALES &amp; MARKETING</a><a>MERIDIAN AWARDS</a><a>REFRENCES</a><a>CAREERS</a><a>ABOUT</a><a>CONTACT US</a>
  </nav>

  <section class="hero">
    <h1 class="hero-title">AUTOMOBILE PARTS</h1>
    <div class="hero-sub">MANUFACTURE &amp; REPAIRING</div>
    <p class="hero-copy">Lorem ipsum dolor sit amet consectetuer adipiscing elit Nam cursus Morbi ut mi Nullam enim leo egestas id condimentum</p>
    <div class="dots"><i></i><i></i><i></i><i></i></div>
    <div class="hero-art" role="img" aria-label="Chrome engine pistons and crankshaft assembly"></div>
  </section>

  <section class="tiles">
    <div class="tile">
      <div class="tile-photo" role="img" aria-label="Shelves stocked with automotive parts" style="background:linear-gradient(160deg,#8a8682,#4a443e 55%,#2a2622)"></div>
      <div class="tile-caption">Automotive Parts<svg width="12" height="20" viewBox="0 0 12 20"><path d="M2 2l8 8-8 8" fill="none" stroke="#fff" stroke-width="2"/></svg></div>
    </div>
    <div class="tile">
      <div class="tile-photo" role="img" aria-label="Mechanic working under a car bonnet" style="background:linear-gradient(160deg,#3a4a5e,#5c6470 50%,#262626)"></div>
      <div class="tile-caption">Vehicle Repair Specialists<svg width="12" height="20" viewBox="0 0 12 20"><path d="M2 2l8 8-8 8" fill="none" stroke="#fff" stroke-width="2"/></svg></div>
    </div>
    <div class="tile">
      <div class="tile-photo" role="img" aria-label="Close view of engine belts and pulleys" style="background:linear-gradient(160deg,#9aa2ac,#5e6670 55%,#3a3e44)"></div>
      <div class="tile-caption">Parts Manufacturers<svg width="12" height="20" viewBox="0 0 12 20"><path d="M2 2l8 8-8 8" fill="none" stroke="#fff" stroke-width="2"/></svg></div>
    </div>
  </section>

  <section class="about">
    <h2>ABOUT OUR COMPANY</h2>
    <p>Morbi diam mauris viverra in gravida eu mattis in ante Morbi eget arcu Morbi porta libero id ullamcorper nonummy nibh ligula pulvinar metus eget consectetuer augue nisi quis lacus Ut ac mi quis lacus</p>
    <p class="tight">Mollis aliquam Curabitur iaculis tempus eros Curabitur vel mi sit amet magna malesuada ultrices Ut nisi erat fermentum vel congue id euismod in elit</p>
    <p>Fusce ultricies orci ac feugiat suscipit leo massa sodales velit et scelerisque mi tortor at ipsum</p>
  </section>

  <section class="video">
    <div class="video-frame" role="img" aria-label="Car interior with exposed dashboard wiring">
      <svg class="play" width="34" height="34" viewBox="0 0 34 34"><circle cx="17" cy="17" r="16" fill="#fff" fill-opacity=".9"/><path d="M13 10l11 7-11 7z" fill="#444"/></svg>
    </div>
    <h3>Watch Our Video</h3>
    <p>Curabitur vel mi sit amet magna malesuada ultri-ces Ut nisi erat fermentum vel congue</p>
  </section>

  <section class="news">
    <h3>News &amp; Blog Post</h3>
    <h4>Morbi ornare gravida</h4>
    <p>Integer congue augue et malesuada iaculis ipsum dui aliquet felis at elementum elit at tellus nec</p>
    <span class="more">Read More</span>
    <h4>Class aptent taciti sociosqu</h4>
    <p>Morbi ornare gravida elit Integer congue augue et malesuada iaculis ipsum dui aliquet felis at cursus magna nisl nec elit Praesent elementum</p>
    <span class="more">Read More</span>
  </section>

  <div class="badges">
    <i class="badge" style="width:30px"></i><i class="badge" style="width:20px"></i><i class="badge" style="width:32px"></i><i class="badge" style="width:20px"></i><i class="badge" style="width:28px"></i><i class="badge" style="width:30px"></i><i class="badge" style="width:28px"></i><i class="badge" style="width:28px"></i><i class="badge" style="width:52px;height:8px"></i><i class="badge" style="width:52px;height:8px"></i><i class="badge" style="width:26px;height:10px"></i><i class="badge" style="width:30px;height:10px"></i><i class="badge" style="width:22px"></i><i class="badge" style="width:18px"></i><i class="badge" style="width:22px"></i>
  </div>

  <footer class="footer">
    <div class="col" style="left:157px"><h5>Company</h5><a>Home</a><a>About Us</a><a>Our Mission</a></div>
    <div class="divider" style="left:245px"></div>
    <div class="col" style="left:276px"><h5>Services</h5><a>Automobile Repair</a><a>Automobile Parts</a><a>Manufacturing</a></div>
    <div class="divider" style="left:376px"></div>
    <div class="col" style="left:403px"><h5>Resources</h5><a>Careers</a><a>Clients</a><a>Partners</a><a>References</a></div>
    <div class="divider" style="left:495px"></div>
    <div class="col" style="left:527px"><h5>Support</h5><a>Term of Use</a><a>Awards</a><a>Contact Us</a></div>
    <div class="divider" style="left:624px"></div>
    <div class="col" style="left:654px"><h5>Get in touch</h5><p>Please connect with us on followings.</p>
      <div class="social"><i></i><i></i><i></i><i></i></div>
    </div>
  </footer>
  <div class="legal"><span>© 2014 Company Name</span><span>All right reserved</span><span>Term of Use</span></div>
</div>
</body>
</html>
```